Lunelle Rosa Hair Fancy Business Card’s

I want my business cards to be elite, original and very classy. I want the business cards to match the colors of my logo and to match the design posted. I would love the design of the picture I posted

I want the card all white .
The dripping on the top of the card I want it to match the pink color in my logo that’s also posted .
I need my logo on the business card !
I need my Instagram- @lunelle.rosa.hair__
And my phone number - 555 207 3962

Target Market(s)

My target market is young woman age 23 to older woman to the age of 65
I want both older and younger women to love my design . I don’t want any cheap looking business cards

Industry/Entity Type

Hair And Beauty

Contact Information for Business Card

Add my logo
Add my Instagram- @lunelle.rosa.hair__
My number - 555 207 3962
My website- www.lunellerosahair.example

Font styles to use
Serif
Script

Colors
ffffff
e667a6
e34298

Requirements
Must have
• The business cards must have my logo, my number , my website, and my Instagram!
Nice to have
• Nice to have glitter words that match my logo
• The business cards must look classy and mature
• I want them to be very unique!!
Should not have
• Should not have any colors that doesn’t match my logo ! This is very important! Please

```html
<!DOCTYPE html>
<html lang="en">
<head>
<meta charset="utf-8">
<title>Lunelle Rosa Hair – Business Card</title>
<link rel="stylesheet" href="https://fonts.googleapis.com/css2?family=Lato:wght@400;700&display=swap">
<style>
  :root {
    --backdrop: #d9d9dc;
    --card-dark: #1f1f21;
    --card-light: #f4f4f4;
    --pink: #e34298;
    --pink-soft: #e667a6;
    --ink: #2b2b2b;
    --rule: #d6d6d6;
  }
  * { margin: 0; padding: 0; box-sizing: border-box; }
  html, body {
    width: 1200px;
    height: 1015px;
    overflow: hidden;
    background: var(--backdrop);
    font-family: "Lato", Arial, sans-serif;
  }
  .sheet {
    width: 1200px;
    height: 1015px;
    display: flex;
    flex-direction: column;
    align-items: center;
    justify-content: center;
    gap: 60px;
  }
  .card {
    position: relative;
    width: 700px;
    height: 400px;
    overflow: hidden;
    box-shadow: 0 6px 18px rgba(0,0,0,0.18);
  }

  /* Front */
  .card--front { background: var(--card-dark); }
  .card--front .brand-name {
    position: absolute;
    left: 0; right: 0;
    top: 130px;
    text-align: center;
    font-weight: 700;
    font-size: 52px;
    letter-spacing: 2px;
    color: var(--pink);
  }
  .card--front .accent-band {
    position: absolute;
    left: 0; right: 0;
    top: 276px;
    height: 24px;
    background: var(--pink);
  }

  /* Back */
  .card--back { background: var(--card-light); }
  .card--back .brand-name {
    position: absolute;
    left: 30px;
    top: 150px;
    width: 290px;
    font-weight: 700;
    font-size: 32px;
    line-height: 1.15;
    color: var(--pink);
    text-align: center;
    white-space: nowrap;
  }
  .card--back .divider {
    position: absolute;
    left: 338px;
    top: 40px;
    width: 1px;
    height: 190px;
    background: var(--rule);
  }
  .contact-list {
    position: absolute;
    left: 362px;
    right: 20px;
    top: 62px;
    list-style: none;
  }
  .contact-list li {
    display: flex;
    align-items: center;
    gap: 10px;
    font-size: 18px;
    color: var(--ink);
    margin-bottom: 14px;
    white-space: nowrap;
  }
  .contact-list li.social { margin-top: 22px; }
  .contact-icon { width: 24px; height: 24px; flex: none; }
  .card--back .base-band {
    position: absolute;
    left: 0; right: 0;
    bottom: 0;
    height: 130px;
    background: var(--pink);
  }
</style>
</head>
<body>
  <main class="sheet">
    <section class="card card--front" aria-label="Card front">
      <div class="brand-name">Lunelle Rosa Hair</div>
      <div class="accent-band"></div>
    </section>

    <section class="card card--back" aria-label="Card back">
      <div class="brand-name">Lunelle Rosa Hair</div>
      <div class="divider"></div>
      <ul class="contact-list">
        <li>
          <svg class="contact-icon" viewBox="0 0 26 26" aria-hidden="true">
            <circle cx="13" cy="13" r="12" fill="var(--pink)"/>
            <path d="M9 7.5c.6-.4 1.3-.3 1.7.3l1.2 1.8c.3.5.2 1.1-.2 1.5l-.8.7c.6 1.4 1.7 2.6 3.1 3.3l.7-.8c.4-.4 1-.5 1.5-.2l1.8 1.2c.6.4.7 1.2.3 1.7l-.8 1c-.6.7-1.6.9-2.5.5-3-1.3-5.3-3.6-6.6-6.6-.4-.9-.2-1.900.5-2.5z" fill="#fff"/>
          </svg>
          <span>555 207 3962</span>
        </li>
        <li>
          <svg class="contact-icon" viewBox="0 0 26 26" aria-hidden="true">
            <circle cx="13" cy="13" r="12" fill="var(--pink)"/>
            <g fill="none" stroke="#fff" stroke-width="1.4">
              <circle cx="13" cy="13" r="7"/>
              <ellipse cx="13" cy="13" rx="3" ry="7"/>
              <line x1="6" y1="13" x2="20" y2="13"/>
              <line x1="7.2" y1="9.5" x2="18.8" y2="9.5"/>
              <line x1="7.2" y1="16.5" x2="18.8" y2="16.5"/>
            </g>
          </svg>
          <span>www.lunellerosahair.example</span>
        </li>
        <li class="social">
          <svg class="contact-icon" viewBox="0 0 26 26" aria-hidden="true">
            <circle cx="13" cy="13" r="12" fill="var(--pink)"/>
          </svg>
          <span>@lunelle.rosa.hair__</span>
        </li>
      </ul>
      <div class="base-band"></div>
    </section>
  </main>
</body>
</html>
```